Copper Lantern

Need a business card for our restaurant. Restaurant and Bar in the mountains of North Idaho. Rustic looking card

rustic design, wood and metal looking, primarily neutral colors

• Name, address, phone number, website, email address

```html
<!DOCTYPE html>
<html lang="en">
<head>
<meta charset="utf-8">
<title>Copper Lantern – Business Card</title>
<link href="https://fonts.googleapis.com/css2?family=Montserrat:wght@400;500;700&display=swap" rel="stylesheet">
<style>
  :root {
    --backdrop: #e9e7e4;
    --card: #ffffff;
    --ink: #111111;
    --ink-soft: #444444;
    --card-shadow: rgba(0,0,0,0.14);
  }
  * { margin: 0; padding: 0; box-sizing: border-box; }
  html, body { width: 1200px; height: 900px; overflow: hidden; }
  body {
    background: var(--backdrop);
    font-family: "Montserrat", sans-serif;
    color: var(--ink);
    position: relative;
  }
  .card {
    position: absolute;
    left: 285px;
    width: 630px;
    height: 360px;
    background: var(--card);
    border-radius: 34px;
    box-shadow: 0 10px 26px var(--card-shadow);
  }
  .card--front { top: 70px; }
  .card--back { top: 470px; display: flex; align-items: center; justify-content: center; }

  .brand {
    display: flex;
    align-items: center;
    gap: 14px;
  }
  .brand__dot {
    width: 26px; height: 26px;
    border: 3px solid var(--ink);
    border-radius: 50%;
  }
  .brand__name {
    font-weight: 700;
    color: var(--ink);
    letter-spacing: 0.06em;
    text-transform: uppercase;
  }
  .card--front .brand { position: absolute; top: 62px; left: 300px; }
  .card--front .brand__name { font-size: 22px; }
  .card--back .brand__name { font-size: 34px; }
  .card--back .brand__dot { width: 38px; height: 38px; border-width: 4px; }

  .person {
    position: absolute;
    top: 150px;
    right: 342px;
    text-align: right;
  }
  .person__name { font-size: 28px; font-weight: 700; line-height: 1.1; }
  .person__role { font-size: 15px; font-weight: 400; color: var(--ink-soft); margin-top: 6px; }
  .person__address { font-size: 15px; color: var(--ink-soft); margin-top: 22px; white-space: nowrap; }

  .divider {
    position: absolute;
    left: 310px;
    top: 176px;
    width: 2px;
    height: 66px;
    background: var(--ink);
  }

  .contacts {
    position: absolute;
    left: 330px;
    top: 178px;
    list-style: none;
    font-size: 16px;
    line-height: 1.6;
    color: var(--ink);
  }
  .contacts li { display: flex; align-items: center; gap: 10px; }
  .contacts svg { width: 14px; height: 14px; fill: var(--ink); flex: none; }
</style>
</head>
<body>

<section class="card card--front" aria-label="Business card front">
  <div class="brand">
    <span class="brand__dot"></span>
    <span class="brand__name">Copper Lantern</span>
  </div>

  <div class="person">
    <p class="person__name">Owen Hartley</p>
    <p class="person__role">Managing Director</p>
    <p class="person__address">Your address, City State, Zip 1234</p>
  </div>

  <span class="divider"></span>

  <ul class="contacts">
    <li>
      <svg viewBox="0 0 16 16" aria-hidden="true"><path d="M3 1h3l1.5 4-2 1.3a9 9 0 0 0 4.2 4.2L11 8.5l4 1.5v3a2 2 0 0 1-2 2A12 12 0 0 1 1 3a2 2 0 0 1 2-2z"/></svg>
      123 456 789
    </li>
    <li>
      <svg viewBox="0 0 16 16" aria-hidden="true"><path d="M1 3h14v10H1z" fill="none" stroke="#111" stroke-width="1.6"/><path d="M1 3l7 6 7-6" fill="none" stroke="#111" stroke-width="1.6"/></svg>
      info@yourgmail.com
    </li>
    <li>
      <svg viewBox="0 0 16 16" aria-hidden="true"><circle cx="8" cy="8" r="6.5" fill="none" stroke="#111" stroke-width="1.6"/><ellipse cx="8" cy="8" rx="2.8" ry="6.5" fill="none" stroke="#111" stroke-width="1.3"/><path d="M1.5 8h13" stroke="#111" stroke-width="1.3"/></svg>
      www.yourwebsite.com
    </li>
  </ul>
</section>

<section class="card card--back" aria-label="Business card back">
  <div class="brand">
    <span class="brand__dot"></span>
    <span class="brand__name">Copper Lantern</span>
  </div>
</section>

</body>
</html>
```